Podcast Art for Bright Belly Radio: Rising above Daily Flares

Read carefully Please. Most submittals so far have not read this.

We're looking for stunning, eye-catching, innovative yet simple podcast art for our first Podcast

Background should be solid, one color

Bright Belly Radio: Rising beyond Daily Flares
with Marcus Telford

Use our Brand Guide including logo, colors, and font
https://lnk.example-short.net/BBR2020StyleKit

Some Podcast Covers I like: https://casts.wavelane-audio.net/

Optional: Captain Flush graphic included above and/or my headshot uploaded below

As you can see humor / medutainment is part of the brand. As we are talking serious topic such as a disease many suffer from you can see the humor in the logo and "captain flush" . Here is the monologue for the first episode to give you a deeper feel on the content

https://files.papermoor-docs.net/doc/7qR_Lk2mWz9PdXc4VtBn8JhYs3FaEo6GuKwTn/edit?share=link

Target Market(s)

Those who suffer from gut issues, are diagnosed with inflammatory bowel disease(IBD), Crohn's Disease or Ulcerative Colitis - also their coaches, doctors, practitioners so functional or integrative medicine doctors/coaches, gastroenterologists etc.

Industry/Entity Type

Health And Wellness

Font styles to use
Other font styles liked:
• Primary: Oswald bold. Secondary: Oswald Medium or light

Requirements
Must have
• 3000 x 3000 pixels
Simple and eye-catching
Brand Guide Logo
Brand Guide Font
Brand Guide Colors including accent color(s)
I did not select colors below because I have included our Brand guide. Please use the exact colors there.
Nice to have
• Maybe my headshot and/or the captain flush graphic - if not too busy and still looks good
Should not have
• - Look busy
- Reverse Logo
- Not follow the Brand Guide
- Anything in the background but one solid color from the brief

```html
<!DOCTYPE html>
<html lang="en">
<head>
<meta charset="utf-8">
<title>Bright Belly Radio – Podcast Cover Options</title>
<link href="https://fonts.googleapis.com/css2?family=Oswald:wght@500;700&display=swap" rel="stylesheet">
<style>
  :root {
    --page: #ffffff;
    --sun: #f2e56f;
    --berry: #d9398a;
    --navy: #1f4e8c;
    --sky: #bfe4f6;
    --ink: #111111;
  }
  * { box-sizing: border-box; margin: 0; padding: 0; }
  html, body {
    width: 1200px;
    height: 728px;
    overflow: hidden;
    background: var(--page);
    font-family: "Oswald", "Arial Narrow", sans-serif;
  }
  .board {
    position: relative;
    width: 1200px;
    height: 728px;
    display: flex;
    justify-content: center;
    gap: 60px;
    padding-top: 56px;
  }
  .option {
    width: 540px;
    display: flex;
    flex-direction: column;
    align-items: flex-end;
  }
  .cover {
    position: relative;
    width: 540px;
    height: 540px;
    overflow: hidden;
  }
  .cover--sun { background: var(--sun); }
  .cover--berry { background: var(--berry); }

  .cover__mark {
    position: absolute;
    left: 42px;
    top: 44px;
    width: 230px;
    display: flex;
    flex-direction: column;
    color: var(--navy);
    font-weight: 700;
    text-transform: uppercase;
    line-height: 1.08;
  }
  .cover__mark span { font-size: 72px; }

  .cover__title {
    position: absolute;
    right: 30px;
    bottom: 62px;
    width: 225px;
    text-align: right;
    font-weight: 700;
    font-size: 38px;
    line-height: 1.12;
  }
  .cover__host {
    display: block;
    font-weight: 500;
    font-size: 18px;
    line-height: 1.3;
  }
  .cover--sun .cover__title { color: var(--berry); }
  .cover--berry .cover__title { color: var(--sun); }
  .cover--berry .cover__host { color: var(--sky); }

  .option__label {
    margin-top: 10px;
    font-weight: 700;
    font-size: 34px;
    color: var(--ink);
    line-height: 1.1;
  }
</style>
</head>
<body>
  <main class="board">
    <section class="option">
      <div class="cover cover--sun">
        <div class="cover__mark" aria-label="Bright Belly Radio">
          <span>Bright</span><span>Belly</span><span>Radio</span>
        </div>
        <p class="cover__title">Rising beyond<br>Daily Flares
          <span class="cover__host">with Marcus Telford</span>
        </p>
      </div>
      <p class="option__label">Option 1</p>
    </section>

    <section class="option">
      <div class="cover cover--berry">
        <div class="cover__mark" aria-label="Bright Belly Radio">
          <span>Bright</span><span>Belly</span><span>Radio</span>
        </div>
        <p class="cover__title">Rising beyond<br>Daily Flares
          <span class="cover__host">with Marcus Telford</span>
        </p>
      </div>
      <p class="option__label">Option 2</p>
    </section>
  </main>
</body>
</html>
```